Marwick Law Letterhead

We need a new letterhead design for a Law Firm. The address for the law firm is 1475 Calloway Street, Suite 210, Houston, Texas 77041. Phone Number: 832-361-9027; Fax Number: 832-614-7359. The logo is uploaded to the project.

```html
<!DOCTYPE html>
<html lang="en">
<head>
<meta charset="utf-8">
<title>Marwick Law Letterhead</title>
<link rel="stylesheet" href="https://fonts.googleapis.com/css2?family=Montserrat:wght@400;500&display=swap">
<style>
  :root {
    --navy: #1f2d5c;
    --red: #c8141e;
    --ink: #2a2a2a;
    --paper: #ffffff;
    --backdrop: #e8e8e8;
  }
  * { margin: 0; padding: 0; box-sizing: border-box; }
  html, body {
    width: 1154px; height: 1200px; overflow: hidden;
    background: var(--backdrop);
    font-family: "Montserrat", Arial, sans-serif;
    color: var(--ink);
  }
  .letterhead {
    position: absolute; left: 163px; top: 21px;
    width: 828px; height: 1158px;
    background: var(--paper);
    box-shadow: 0 6px 24px rgba(0,0,0,0.25);
  }
  .brand {
    position: absolute; left: 32px; top: 82px;
    display: flex; align-items: center; gap: 14px;
  }
  .brand-mark {
    width: 46px; height: 46px; background: var(--navy);
  }
  .brand-name {
    font-size: 34px; font-weight: 500; color: var(--navy);
    letter-spacing: 0.5px;
  }
  .contact-line {
    position: absolute; left: 77px; top: 188px;
    display: flex; align-items: center; gap: 8px;
    font-size: 14.6px; color: #111;
    white-space: nowrap;
  }
  .contact-line .address { margin-right: 8px; }
  .contact-line svg { width: 15px; height: 15px; }
  .contact-line .number { margin-right: 4px; }
  .rule {
    position: absolute; left: 30px; width: 767px; height: 2px;
  }
  .rule.red { top: 222px; background: var(--red); }
  .rule.navy { top: 228px; background: var(--navy); }
  .recipient {
    position: absolute; left: 31px; top: 312px;
    font-size: 14px; line-height: 20.7px;
  }
  .body-copy {
    position: absolute; left: 32px; top: 399px; width: 768px;
    font-size: 13.9px; line-height: 20.6px; text-align: justify;
  }
  .body-copy p + p { margin-top: 20.6px; }
  .closing {
    position: absolute; left: 30px; top: 891px;
    font-size: 17px;
  }
  .signature {
    position: absolute; left: 28px; top: 922px;
    width: 94px; height: 26px;
    background: linear-gradient(90deg, #3a3a3a, #6a6a6a);
    border-radius: 3px; opacity: 0.55;
  }
</style>
</head>
<body>
  <main class="letterhead">
    <header>
      <div class="brand">
        <div class="brand-mark"></div>
        <div class="brand-name">Marwick Law</div>
      </div>
      <div class="contact-line">
        <span class="address">1475 Calloway Street, Suite 210, Houston, Texas 77041</span>
        <svg viewBox="0 0 24 24" aria-hidden="true"><path fill="var(--red)" d="M6.6 10.8a15.5 15.5 0 0 0 6.6 6.6l2.2-2.2c.3-.3.7-.4 1-.2 1.1.4 2.3.6 3.6.6.6 0 1 .4 1 1V20c0 .6-.4 1-1 1A17 17 0 0 1 3 4c0-.6.4-1 1-1h3.5c.6 0 1 .4 1 1 0 1.3.2 2.5.6 3.6.1.3 0 .7-.2 1z"/></svg>
        <span class="number">832-361-9027</span>
        <svg viewBox="0 0 24 24" aria-hidden="true"><path fill="var(--red)" d="M7 3h10v4H7zM4 8h16a2 2 0 0 1 2 2v6h-4v5H6v-5H2v-6a2 2 0 0 1 2-2zm4 7v4h8v-4z"/></svg>
        <span class="number">832-614-7359</span>
      </div>
      <div class="rule red"></div>
      <div class="rule navy"></div>
    </header>

    <address class="recipient" style="font-style:normal">
      Mr/s<br>First Name and Last Name<br>Company Name<br>Address
    </address>

    <section class="body-copy">
      <p>Lorem ipsum dolor sit amet,consectetur adipiscing sed do eiusmod tempor incididunt laboreet dolore magna aliqua.Ut enim ad minim.veniam, quis nostrud exercitation ullamco laboris nisi ut aliquip exea commodo consequat.Lorem ipsum dolor sit amet,consectetur adipiscing sed do eiusmod tempor incididunt.labore et dolore magna aliqua. Ut enim</p>
      <p>Lorem ipsum dolor sit amet, consectetur adipiscing sed do eiusmod tempor incididunt labore et dolore magna aliqua. Ut enim ad minim veniam, quis nostrud exercitation ullamco laboris nisi ut aliquip exea commodo consequat.Duis aute irure dolor in reprehenderit in voluptate velit esse cillum irure dolor in reprehenderit in voluptate velit esse irure</p>
      <p>Lorem ipsum dolor sit amet, consectetur adipiscing sed do eiusmod tempor incididunt labore et dolore magna aliqua. consequat. Duis aute irure dolor in.reprehenderit in voluptate velit esse cillum dolore eu fugiat nulla pariatur. Excepteur sint occaecat cupidatat non proident, sunt in culpa qui officia deserunt mollit,</p>
      <p>Lorem ipsum dolor sit amet, consectetur adipiscing sed do eiusmod tempor incididunt labore et dolore magna aliqua. Ut enim Lorem ipsum dolor sit amet, consectetur adipiscing sed do eiusmod tempor incididunt labore et dolore magna aliqua. Ut enim Lorem ipsum aliqua.ipsum</p>
      <p>Lorem ipsum dolor sit amet, consectetur adipiscing sed do eiusmod tempor incididunt labore et dolore magna aliqua. Ut enim ad minim veniam, quis nostrud exercitation ullamco laboris nisi ut aliquip exea commodo consequat.Duis aute irure dolor in reprehenderit in voluptate velit esse cillum irure dolor in reprehenderit in voluptate velit esse irure</p>
    </section>

    <footer>
      <div class="closing">Regards</div>
      <div class="signature" role="img" aria-label="Handwritten signature"></div>
    </footer>
  </main>
</body>
</html>
```